Company identity deisgn should support 2 languages

I would like to get our company identity design
This includes the following only
Business Cards 2 languages Arabic and English
Email signature
Letterhead
Linkedin profile images
Attached is the logo in Ai format

Requirements
Must have
• For business card
Must have
Name and Adrees in arabic
Name and Address in english
You might use both side of the card
Should not have
• Any pictures other than the logo

```html
<!DOCTYPE html>
<html lang="en">
<head>
<meta charset="utf-8">
<title>Quillmere Systems – Business Cards</title>
<link href="https://fonts.googleapis.com/css2?family=Poppins:wght@400;500;600&family=Noto+Sans+Arabic:wght@400;600&display=swap" rel="stylesheet">
<style>
  :root {
    --bg: #8a8a8a;
    --card: #ffffff;
    --brand: #1277c0;
    --ink: #3c3c3c;
    --muted: #8c8c8c;
    --rule: #c9c9c9;
  }
  html, body { margin: 0; padding: 0; overflow: hidden; }
  body {
    width: 1200px; height: 1200px;
    background: var(--bg);
    font-family: "Poppins", sans-serif;
    position: relative;
  }
  .card {
    position: absolute;
    left: 262px;
    width: 686px; height: 392px;
    background: var(--card);
    border-radius: 30px;
    overflow: hidden;
  }
  .card--en { top: 165px; }
  .card--ar { top: 653px; }
  .card__band {
    position: absolute; left: 0; right: 0; bottom: 0;
    height: 17px; background: var(--brand);
  }
  .brand {
    position: absolute; left: 32px; top: 178px;
    display: flex; align-items: center; gap: 12px;
  }
  .brand__mark { width: 30px; height: 30px; background: var(--brand); border-radius: 50%; flex: none; }
  .brand__name {
    font-weight: 500; font-size: 23px; letter-spacing: 0.5px;
    color: var(--brand); white-space: nowrap;
  }
  .divider {
    position: absolute; left: 364px; top: 90px;
    width: 1px; height: 213px; background: var(--rule);
  }
  .details { position: absolute; left: 389px; top: 88px; width: 290px; }
  .details__name {
    margin: 0; font-weight: 600; font-size: 22px; line-height: 28px;
    color: var(--brand); letter-spacing: .3px;
  }
  .details__title { margin: 0 0 10px; font-size: 16px; line-height: 20px; color: var(--muted); }
  .details__address { margin: 0 0 12px; font-size: 16px; line-height: 20px; color: var(--ink); }
  .details--ar .details__name { font-family: "Noto Sans Arabic", sans-serif; font-size: 22px; line-height: 28px; letter-spacing: 0; }
  .details--ar .details__title { font-family: "Noto Sans Arabic", sans-serif; margin-bottom: 12px; }
  .details--ar .details__address { font-family: "Noto Sans Arabic", sans-serif; font-size: 15px; line-height: 22px; margin-bottom: 10px; }
  .contacts { list-style: none; margin: 0; padding: 0; }
  .contacts li {
    display: flex; align-items: center; gap: 9px;
    font-size: 16px; line-height: 19.5px; color: var(--ink); white-space: nowrap;
  }
  .contacts svg { width: 13px; height: 13px; fill: var(--brand); flex: none; }
</style>
</head>
<body>

<section class="card card--en">
  <div class="brand"><span class="brand__mark"></span><span class="brand__name">QUILLMERE SYSTEMS</span></div>
  <div class="divider"></div>
  <div class="details">
    <h1 class="details__name">DANIEL HAYES</h1>
    <p class="details__title">President</p>
    <p class="details__address">4210 Oakridge Avenue<br>Juneau, Alaska 99801</p>
    <ul class="contacts">
      <li><svg viewBox="0 0 16 16"><path d="M3.5 1l3 3-1.8 2a9 9 0 0 0 5.3 5.3l2-1.8 3 3-2 2C6 14.5 1.5 10 1.5 3z"/></svg>555-214-7730</li>
      <li><svg viewBox="0 0 16 16"><path d="M4 0h8a1 1 0 0 1 1 1v14a1 1 0 0 1-1 1H4a1 1 0 0 1-1-1V1a1 1 0 0 1 1-1zm1 2v11h6V2z"/></svg>555-608-3142</li>
      <li><svg viewBox="0 0 16 16"><path d="M4 1h8v4H4zM1 6h14v6h-2v3H3v-3H1zm4 5v3h6v-3z"/></svg>555-391-2586</li>
      <li><svg viewBox="0 0 16 16"><path d="M1 3h14v10H1zm1.5 1.5L8 9l5.5-4.5z"/></svg>info@quillmeresystems.com</li>
      <li><svg viewBox="0 0 16 16"><circle cx="8" cy="8" r="7"/></svg>www.quillmeresystems.com</li>
    </ul>
  </div>
  <div class="card__band"></div>
</section>

<section class="card card--ar">
  <div class="brand"><span class="brand__mark"></span><span class="brand__name">QUILLMERE SYSTEMS</span></div>
  <div class="divider"></div>
  <div class="details details--ar">
    <h1 class="details__name" lang="ar" dir="rtl" style="text-align:left">دانيال هايز</h1>
    <p class="details__title" lang="ar" dir="rtl" style="text-align:left">رئيس</p>
    <p class="details__address" lang="ar"><span dir="rtl">4210 أوكريدج أفينيو</span><br><span dir="rtl">جونو ، ألاسكا 99801</span></p>
    <ul class="contacts">
      <li><svg viewBox="0 0 16 16"><path d="M3.5 1l3 3-1.8 2a9 9 0 0 0 5.3 5.3l2-1.8 3 3-2 2C6 14.5 1.5 10 1.5 3z"/></svg>555-214-7730</li>
      <li><svg viewBox="0 0 16 16"><path d="M4 0h8a1 1 0 0 1 1 1v14a1 1 0 0 1-1 1H4a1 1 0 0 1-1-1V1a1 1 0 0 1 1-1zm1 2v11h6V2z"/></svg>555-608-3142</li>
      <li><svg viewBox="0 0 16 16"><path d="M4 1h8v4H4zM1 6h14v6h-2v3H3v-3H1zm4 5v3h6v-3z"/></svg>555-391-2586</li>
      <li><svg viewBox="0 0 16 16"><path d="M1 3h14v10H1zm1.5 1.5L8 9l5.5-4.5z"/></svg>info@quillmeresystems.com</li>
      <li><svg viewBox="0 0 16 16"><circle cx="8" cy="8" r="7"/></svg>www.quillmeresystems.com</li>
    </ul>
  </div>
  <div class="card__band"></div>
</section>

</body>
</html>
```